Bramblewood Card Company Business Cards

We are a trading card store with Glimmorax, sports and other TCG cards, we need a business card design that encompasses a clean cut, modern style with a retro flare. website is bramblewoodcardco.com for reference. Can utilize a comic book era feel or a more modern outdoor feel to utilize the "Pacific Northwest" elements of tress, mountains, etc.

Industry/Entity Type

Trading cards and collectibles

Contact Information for Business Card

business name, email address, phone number, name, owner job title

Font styles to use
Sans Serif

```html
<!DOCTYPE html>
<html lang="en">
<head>
<meta charset="utf-8">
<title>Bramblewood Card Company – Business Card</title>
<link href="https://fonts.googleapis.com/css2?family=Montserrat:wght@800&family=Josefin+Sans:wght@400;600&display=swap" rel="stylesheet">
<style>
  :root {
    --page: #ececec;
    --sky: #20bfe0;
    --sky-light: #5ccbe8;
    --slate: #767676;
    --slate-dark: #6a6a6a;
    --white: #ffffff;
  }
  html, body {
    margin: 0;
    width: 1200px;
    height: 1200px;
    overflow: hidden;
    background: var(--page);
  }
  .card {
    position: absolute;
    top: 220px;
    width: 455px;
    height: 758px;
    box-shadow: 0 6px 18px rgba(0,0,0,.18);
  }
  .card--front { left: 115px; }
  .card--back  { left: 628px; }
  .card svg { display: block; width: 100%; height: 100%; }
  .company-title {
    font-family: "Montserrat", sans-serif;
    font-weight: 800;
    font-size: 60px;
    fill: var(--white);
  }
  .person-name {
    font-family: "Josefin Sans", sans-serif;
    font-weight: 400;
    font-size: 54px;
    fill: var(--white);
  }
  .job-title {
    font-family: "Josefin Sans", sans-serif;
    font-weight: 400;
    font-size: 36px;
    fill: var(--white);
  }
  .contact-line {
    font-family: "Josefin Sans", sans-serif;
    font-weight: 400;
    font-size: 40px;
    fill: var(--white);
  }
  .contact-line--email {
    font-family: "Montserrat", sans-serif;
    font-weight: 800;
    font-size: 34px;
  }
  .brand-name {
    font-family: "Montserrat", sans-serif;
    font-weight: 800;
    font-size: 52px;
    fill: var(--slate);
  }
</style>
</head>
<body>

<div class="card card--front">
  <svg viewBox="0 0 732 1220" xmlns="http://www.w3.org/2000/svg">
    <defs>
      <radialGradient id="front-glow" cx="0.45" cy="0.7" r="0.6">
        <stop offset="0" stop-color="#5ccbe8"/>
        <stop offset="1" stop-color="#20bfe0"/>
      </radialGradient>
      <linearGradient id="header-shade" x1="0" y1="0" x2="0" y2="1">
        <stop offset="0" stop-color="#6e6e6e"/>
        <stop offset="1" stop-color="#7a7a7a"/>
      </linearGradient>
    </defs>

    <rect class="card-base" width="732" height="1220" fill="var(--sky)"/>

    <rect class="burst-area" role="img" aria-label="Comic burst rays with halftone dots"
          x="0" y="540" width="732" height="680" fill="url(#front-glow)"/>

    <rect class="header-area" role="img" aria-label="Grey comic speech bubble header with white swoosh"
          x="0" y="0" width="732" height="440" fill="url(#header-shade)"/>

    <text class="company-title" x="366" y="203" text-anchor="middle">BRAMBLEWOOD</text>
    <text class="company-title" x="366" y="266" text-anchor="middle">CARD COMPANY</text>

    <text class="person-name" x="366" y="686" text-anchor="middle">Your Name</text>

    <g class="title-ribbon">
      <polygon points="238,720 270,720 270,775 250,775 225,772 245,748" fill="var(--slate)"/>
      <polygon points="494,720 462,720 462,775 482,775 507,772 487,748" fill="var(--slate)"/>
      <rect x="258" y="712" width="216" height="58" fill="var(--slate)" stroke="var(--sky)" stroke-width="4"/>
      <text class="job-title" x="366" y="753" text-anchor="middle">Job Title</text>
    </g>

    <g class="contact-phone">
      <g stroke="var(--white)" stroke-width="5">
        <line x1="189" y1="864" x2="330" y2="864"/>
        <line x1="189" y1="874" x2="330" y2="874"/>
        <line x1="405" y1="864" x2="547" y2="864"/>
        <line x1="405" y1="874" x2="547" y2="874"/>
      </g>
      <polygon points="368,843 390,856 390,882 368,895 346,882 346,856" fill="var(--slate)"/>
      <path d="M359 858 q3-3 6 0 l3 5 q1 3-2 5 q3 6 8 9 q2-3 5-2 l5 3 q3 3 0 6 q-4 4-9 2 q-12-6-18-18 q-2-5 2-10 z" fill="var(--white)"/>
      <text class="contact-line" x="368" y="940" text-anchor="middle">123 123 123</text>
    </g>

    <g class="contact-email">
      <g stroke="var(--white)" stroke-width="5">
        <line x1="189" y1="1004" x2="330" y2="1004"/>
        <line x1="189" y1="1014" x2="330" y2="1014"/>
        <line x1="405" y1="1004" x2="547" y2="1004"/>
        <line x1="405" y1="1014" x2="547" y2="1014"/>
      </g>
      <polygon points="368,983 390,996 390,1022 368,1035 346,1022 346,996" fill="var(--slate)"/>
      <rect x="355" y="999" width="26" height="18" rx="2" fill="var(--white)"/>
      <polyline points="355,1000 368,1010 381,1000" fill="none" stroke="var(--slate)" stroke-width="2.5"/>
      <text class="contact-line contact-line--email" x="368" y="1072" text-anchor="middle">name@email.com</text>
    </g>
  </svg>
</div>

<div class="card card--back">
  <svg viewBox="0 0 732 1220" xmlns="http://www.w3.org/2000/svg">
    <defs>
      <radialGradient id="back-glow" cx="0.7" cy="0.3" r="0.7">
        <stop offset="0" stop-color="#5ccbe8"/>
        <stop offset="1" stop-color="#20bfe0"/>
      </radialGradient>
    </defs>

    <rect class="card-base" width="732" height="1220" fill="var(--sky)"/>

    <rect class="burst-area" role="img" aria-label="Comic burst rays with halftone dots"
          x="0" y="0" width="732" height="660" fill="url(#back-glow)"/>

    <text class="brand-name" x="366" y="830" text-anchor="middle">BRAMBLEWOOD</text>
    <text class="brand-name" x="366" y="892" text-anchor="middle">CARD COMPANY</text>
  </svg>
</div>

</body>
</html>
```